Tavel Website

Need a 4 page Drupal website - Home, About Us, Portfolio, Contact for a private equity/venture capital firm and new logo - company name is Tavel Corporation. The design should communicate - stock markets, hedge funds, deal-making, investments. The Portfolio section is to showcase the small companies we invest in. Hoping for something fresh, dynamic, even fun - no cliche financial images of New York. Not technical - but know how use Drupal content management to make text edits, blocks, articles, etc. We don't use any social media - so no chirply, Pagebook or WorkNode links. We need space for a post heron email sign-up form. Need website uploaded to my Corvane web hosting account. First time user of Sketch Plaza - have 3 other company websites that need refreshing.

```html
<!DOCTYPE html>
<html lang="en">
<head>
<meta charset="utf-8">
<title>Tavel Corporation</title>
<link rel="stylesheet" href="https://fonts.googleapis.com/css2?family=Ubuntu:wght@400;500;700&display=swap">
<style>
:root{
  --brand-ink:#1f5bb5;
  --ink:#333;
  --nav:#555;
  --band-top:#4b8ad0;
  --band-bottom:#1c55a2;
  --subscribe:#1b4f9c;
  --line:#ddd;
  --holding:#3a3a3a;
  --footer-top:#f2f2f2;
  --footer-bottom:#e6e6e6;
}
*{margin:0;padding:0;box-sizing:border-box}
html,body{width:963px;height:1200px;overflow:hidden;background:#fff}
body{position:relative;font-family:'Ubuntu',sans-serif;color:var(--ink)}
.abs{position:absolute}

.site-header{left:0;top:0;width:963px;height:78px;background:linear-gradient(#fdfdfd,#ececec);border-bottom:1px solid #d8d8d8}
.brand{left:98px;top:18px}
.brand-name{font-size:23px;font-weight:500;letter-spacing:.2px;line-height:1;color:var(--brand-ink)}
.brand-tag{font-size:10.5px;letter-spacing:1px;color:#444;margin-top:6px}
.main-nav{right:98px;top:32px;display:flex;gap:20px;font-size:13px;color:var(--nav)}

.hero{left:0;top:78px;width:963px;height:386px;background:radial-gradient(ellipse at 48% 58%,#b89a4c 0%,#8a7650 16%,#2b3556 42%,#1c2338 75%,#3a3f4c 100%)}
.hero-arrow{top:170px;width:63px;height:63px;background:rgba(30,30,30,.78);border-radius:3px;display:flex;align-items:center;justify-content:center}
.hero-arrow.prev{left:55px}
.hero-arrow.next{left:843px}

.tips{left:0;top:464px;width:963px;height:311px;background:linear-gradient(var(--band-top),var(--band-bottom));color:#fff}
.tips-title{position:absolute;top:37px;left:0;width:933px;text-align:center;font-size:13.5px;font-weight:500;letter-spacing:.3px}
.tip{position:absolute;top:84px;width:180px}
.tip-head{display:flex;align-items:center;gap:6px;height:48px}
.tip-head h3{font-size:12.5px;font-weight:500}
.tip p{font-size:11px;line-height:19.3px;margin-top:10px;color:#eef3fb}
.tip-btn{display:inline-block;margin-top:23px;width:92px;height:24px;line-height:24px;text-align:center;font-size:11px;color:#333;background:linear-gradient(#fff,#e8e8e8);border-radius:3px;box-shadow:0 1px 2px rgba(0,0,0,.3)}

.portfolio-title{left:0;top:791px;width:963px;text-align:center;font-size:11.5px;font-weight:500;color:#222}
.portfolio-row{left:95px;top:840px;width:780px;height:42px;display:flex;align-items:center;justify-content:space-between}
.holding{font-size:10.5px;font-weight:500;color:var(--holding);white-space:nowrap}

.section-head{font-size:11.5px;font-weight:500;color:#222}
.testimonials{left:109px;top:923px}
.t-arrows{left:452px;top:921px}
.t-photo{left:108px;top:963px;width:83px;height:78px;background:linear-gradient(#9aa3ad,#6f6660)}
.t-mark{left:196px;top:942px;font-size:24px;font-style:italic;color:#333}
.t-quote{left:212px;top:957px;width:255px;font-size:11.3px;line-height:19.3px;color:#333}
.t-name{left:100px;top:1059px;width:99px;text-align:center;font-size:11px;font-weight:500;color:#444;line-height:17px}
.t-name span{display:block;font-weight:400}
.divider{left:484px;top:915px;width:1px;height:175px;background:var(--line)}

.newsletter{left:527px;top:923px}
.nl-text{left:527px;top:958px;width:330px;font-size:11px;line-height:19.5px;color:#333}
.nl-input{left:526px;top:1011px;width:328px;height:35px;border:1px solid #ccc;background:#f7f7f7;font-size:11px;color:#777;padding:10px 9px}
.nl-btn{left:528px;top:1058px;width:95px;height:29px;background:var(--subscribe);color:#fff;font-size:11px;font-weight:500;text-align:center;line-height:29px}

.site-footer{left:0;top:1119px;width:963px;height:81px;background:linear-gradient(var(--footer-top),var(--footer-bottom));text-align:center;color:#444}
.foot-nav{margin-top:20px;font-size:12.5px;word-spacing:2px}
.foot-nav b{font-weight:400;margin:0 12px}
.copy{margin-top:11px;font-size:12px}
</style>
</head>
<body>

<header class="site-header abs">
  <div class="brand abs">
    <div class="brand-name">Tavel Corporation</div>
    <div class="brand-tag">Equity &amp; Venture capital company</div>
  </div>
  <nav class="main-nav abs"><span>Home</span><span>About Us</span><span>Portfolio</span><span>Contact</span></nav>
</header>

<section class="hero abs" role="img" aria-label="Businessman in a dark suit holding a gold piggy bank in open hands">
  <div class="hero-arrow prev abs"><svg width="20" height="30" viewBox="0 0 20 30"><path d="M16 3 4 15l12 12" fill="none" stroke="#fff" stroke-width="3"/></svg></div>
  <div class="hero-arrow next abs"><svg width="20" height="30" viewBox="0 0 20 30"><path d="M4 3l12 12L4 27" fill="none" stroke="#fff" stroke-width="3"/></svg></div>
</section>

<section class="tips abs">
  <h2 class="tips-title">WE GIVE TIPS ON</h2>

  <div class="tip" style="left:95px">
    <div class="tip-head">
      <svg width="52" height="48" viewBox="0 0 52 48" fill="none" stroke="#fff" stroke-width="2"><path d="M2 2v36h22"/><path d="M6 30l8-10 6 6 8-12 8-4"/><path d="M32 6l6-2-1 6"/><circle cx="31" cy="30" r="8"/><path d="M37 36l7 8" stroke-width="3"/></svg>
      <h3>Stock Markets</h3>
    </div>
    <p>Lorem Ipsum is simply dummy text of the printing and typesetting industry. Lorem Ipsum has been the industry's standard dummy</p>
    <span class="tip-btn">Get Tips Now</span>
  </div>

  <div class="tip" style="left:309px">
    <div class="tip-head">
      <svg width="52" height="48" viewBox="0 0 52 48"><rect x="1" y="14" width="40" height="26" fill="#fff"/><rect x="14" y="8" width="14" height="8" fill="none" stroke="#fff" stroke-width="2"/><rect x="30" y="22" width="18" height="24" fill="#fff" stroke="#2a64b0" stroke-width="1.5"/><path d="M34 30h10M34 35h10M34 40h10" stroke="#2a64b0" stroke-width="1.5"/></svg>
      <h3>Hedge Funds</h3>
    </div>
    <p>Lorem Ipsum is simply dummy text of the printing and typesetting industry. Lorem Ipsum has been the industry's standard dummy</p>
    <span class="tip-btn">Get Tips Now</span>
  </div>

  <div class="tip" style="left:491px">
    <div class="tip-head">
      <svg width="40" height="48" viewBox="0 0 40 48" fill="none" stroke="#fff" stroke-width="2"><rect x="3" y="2" width="28" height="36"/><path d="M8 10h18M8 16h18"/><circle cx="21" cy="34" r="8" fill="#fff"/></svg>
      <h3>Deal Making</h3>
    </div>
    <p>Lorem Ipsum is simply dummy text of the printing and typesetting industry. Lorem Ipsum has been the industry's standard dummy</p>
    <span class="tip-btn">Get Tips Now</span>
  </div>

  <div class="tip" style="left:688px">
    <div class="tip-head">
      <svg width="52" height="48" viewBox="0 0 52 48"><circle cx="14" cy="10" r="7" fill="#fff"/><ellipse cx="24" cy="30" rx="18" ry="14" fill="#fff"/></svg>
      <h3>Investments</h3>
    </div>
    <p>Lorem Ipsum is simply dummy text of the printing and typesetting industry. Lorem Ipsum has been the industry's standard dummy</p>
    <span class="tip-btn">Get Tips Now</span>
  </div>
</section>

<h2 class="portfolio-title abs">FEATURED PORTFOLIO</h2>
<div class="portfolio-row abs">
  <span class="holding">Brightfield Solar</span>
  <span class="holding">ionvale</span>
  <span class="holding">marisk</span>
  <span class="holding">PINES</span>
  <span class="holding">Harbin Grid Power</span>
  <span class="holding">Copper Kettle</span>
  <span class="holding">Whitmore</span>
  <span class="holding">LNR</span>
  <span class="holding">Table Group Holdings</span>
  <span class="holding">Halden &amp; Kreuz</span>
</div>

<h2 class="section-head testimonials abs">TESTIMONIALS</h2>
<svg class="t-arrows abs" width="20" height="14" viewBox="0 0 20 14" fill="none" stroke="#666" stroke-width="1.5"><path d="M6 2 1 7l5 5M14 2l5 5-5 5"/></svg>
<div class="t-photo abs" role="img" aria-label="Portrait of a client"></div>
<div class="t-mark abs">“</div>
<p class="t-quote abs">Lorem ipsum dolor sit amet, consectetur adipiscing elit, sed do eiusmod tempor incididunt ut labore et dolore magna aliqua. Ut enim ad minim veniam, quis nostrud exercitation ullamco laboris nisi ut aliquip ex ea commodo</p>
<div class="t-name abs">Arthur Benning<span>London</span></div>
<div class="divider abs"></div>

<h2 class="section-head newsletter abs">NEWSLETTER SIGN UP</h2>
<p class="nl-text abs">Lorem ipsum dolor sit amet, consectetur adipiscing elit, sed do eiusmod tempor incididunt ut labore et dolore magna aliqua.</p>
<div class="nl-input abs">Type Your E-Mail Address</div>
<div class="nl-btn abs">SUBSCRIBE</div>

<footer class="site-footer abs">
  <div class="foot-nav">Home<b>|</b>About Us<b>|</b>Portfolio<b>|</b>Contact</div>
  <div class="copy">© 2014 Company Name ,All RightsReserved</div>
</footer>

</body>
</html>
```